Upscale business cards needed for Board of Directors

We need professional business cards created for members of our family business Board of Directors. We would like these relatively simple and straightforward, but also with a unique element to set them apart. Probably stick with neutral and simple colors - white, grey etc. We need space for the traditional elements, including name, title, address, email/phone number. And we will be creating several from this template so it needs to be template that is easy to switch information in and out of.
Business
See description

```html
<!DOCTYPE html>
<html lang="en">
<head>
<meta charset="utf-8">
<title>Harbourline Holdings – Business Card</title>
<link href="https://fonts.googleapis.com/css2?family=Open+Sans:wght@400;600;800&display=swap" rel="stylesheet">
<style>
  :root {
    --stage: #d9dadc;
    --card-white: #ffffff;
    --card-black: #1c1a1b;
    --ink: #1a1a1a;
    --gold: #a48d63;
    --back-mark: #111011;
  }
  * { box-sizing: border-box; margin: 0; padding: 0; }
  html, body { width: 1200px; height: 864px; overflow: hidden; }
  body {
    background: var(--stage);
    font-family: "Open Sans", Arial, sans-serif;
    position: relative;
  }
  .card {
    position: absolute;
    left: 337px;
    width: 525px;
    height: 300px;
    border-radius: 4px;
    box-shadow: 0 6px 18px rgba(0,0,0,0.18);
  }
  .card--back { top: 96px; background: var(--card-black); }
  .card--front { top: 468px; background: var(--card-white); }

  .company-name {
    position: absolute;
    font-weight: 800;
    text-transform: uppercase;
    line-height: 1.05;
    text-align: center;
  }
  .company-name span { display: block; }
  .company-name .primary { font-size: 36px; letter-spacing: 0.5px; }
  .company-name .secondary { font-size: 20px; letter-spacing: 6px; }

  .card--back .company-name {
    left: 0; right: 0; top: 108px;
    color: var(--back-mark);
  }
  .card--front .company-name {
    right: 34px; top: 40px;
    color: var(--ink);
  }

  .person {
    position: absolute;
    left: 38px; top: 118px;
  }
  .person-name {
    color: var(--gold);
    font-weight: 600;
    font-size: 17px;
    line-height: 1.2;
  }
  .person-title {
    color: var(--ink);
    font-size: 11.5px;
    line-height: 1.3;
  }

  .contact-list {
    position: absolute;
    right: 26px; top: 198px;
    list-style: none;
    text-align: right;
    color: var(--ink);
    font-size: 12.5px;
  }
  .contact-list li {
    display: flex;
    justify-content: flex-end;
    align-items: center;
    gap: 8px;
    height: 21px;
  }
  .contact-list svg { width: 11px; height: 11px; flex: none; }
  .contact-list .address { padding-right: 19px; }
</style>
</head>
<body>

<section class="card card--back" aria-label="Business card back">
  <div class="company-name">
    <span class="primary">Harbourline</span>
    <span class="secondary">Holdings</span>
  </div>
</section>

<section class="card card--front" aria-label="Business card front">
  <div class="company-name">
    <span class="primary">Harbourline</span>
    <span class="secondary">Holdings</span>
  </div>

  <div class="person">
    <p class="person-name">Daniel Hartley</p>
    <p class="person-title">Managing Director</p>
  </div>

  <ul class="contact-list">
    <li>(044)-555-0142
      <svg viewBox="0 0 12 12" aria-hidden="true"><path fill="var(--gold)" d="M2.6 0.8l1.7 1.9-0.9 1.4c0.6 1.4 1.6 2.5 3 3.2l1.4-0.9 2 1.6-0.8 2c-4.6 0-8.2-3.6-8.2-8.2z"/></svg>
    </li>
    <li>hello@harbourline.com
      <svg viewBox="0 0 12 12" aria-hidden="true"><rect x="0.5" y="2" width="11" height="8" rx="1" fill="var(--gold)"/><path d="M1 2.6l5 3.8 5-3.8" fill="none" stroke="#fff" stroke-width="1"/></svg>
    </li>
    <li>www.harbourline.com
      <svg viewBox="0 0 12 12" aria-hidden="true"><circle cx="6" cy="6" r="5.5" fill="var(--gold)"/><path d="M0.8 6h10.4M6 0.5c-2.4 3-2.4 8 0 11M6 0.5c2.4 3 2.4 8 0 11" fill="none" stroke="#fff" stroke-width="0.8"/></svg>
    </li>
    <li class="address">48 Quayside Row, Harbour City, Westland, 204518</li>
  </ul>
</section>

</body>
</html>
```